Web design for Money Service Business (uncoded)

We need a very basic website with 5-6 pages. Home page, Services, Transfer(How to use our service), About us, Contact us, FAQ
Our company name is Norvane Exchange. We are a company that deals with currency exchange and international money transfer. We do cash exchange and international money transfers to bank accounts all over the world. We offer highly competitive exchange rates so usually attract customers who transfer money over $10,000. Our niche is with larger sums of money, the design needs to be professional and communicate trust, security and stability.

```html
<!DOCTYPE html>
<html lang="en">
<head>
<meta charset="utf-8">
<title>Norvane Exchange – International Money Transfer</title>
<link href="https://fonts.googleapis.com/css2?family=Open+Sans:ital,wght@0,400;0,600;0,700;1,400&display=swap" rel="stylesheet">
<style>
:root{
  --orange:#e07b12;
  --orange-dark:#c96a0a;
  --dark:#2b2b2b;
  --darker:#1c1c1c;
  --text:#444;
  --muted:#8a8a8a;
  --rule:#e6e6e6;
  --white:#fff;
  --rate-blue:#1f3f9a;
  --rate-head:#e8ebf4;
}
*{margin:0;padding:0;box-sizing:border-box}
html,body{width:1200px;height:2459px;overflow:hidden}
body{position:relative;background:var(--white);font-family:"Open Sans",Arial,sans-serif;color:var(--text);font-size:10px;line-height:13px}
.abs{position:absolute}

/* header */
.site-header{left:0;top:0;width:1200px;height:88px;background:var(--dark)}
.brand{left:216px;top:25px;height:49px;width:222px;background:var(--white);display:flex;align-items:center;gap:8px;padding:0 12px}
.brand-mark{width:14px;height:14px;background:var(--orange)}
.brand-name{font-size:18px;font-weight:700;color:var(--dark);white-space:nowrap}
.main-nav{left:690px;top:42px;display:flex;gap:24px;font-size:11px;color:#ddd}
.main-nav .active{color:var(--orange)}

/* hero */
.hero{left:0;top:88px;width:1200px;height:399px;
  background:
    radial-gradient(ellipse 60% 40% at 85% 45%,rgba(255,255,255,.55),rgba(255,255,255,0) 70%),
    radial-gradient(ellipse 50% 60% at 10% 90%,rgba(0,0,0,.75),rgba(0,0,0,0) 70%),
    linear-gradient(155deg,#1a1a1a 0%,#3d3d3d 22%,#8e8e8e 42%,#d8d8d8 55%,#9a9a9a 66%,#4a4a4a 82%,#151515 100%)}
.hero-social{left:971px;top:307px;display:flex;flex-direction:column;gap:9px}
.circle-btn{width:40px;height:40px;border-radius:50%;background:var(--orange);display:flex;align-items:center;justify-content:center;box-shadow:inset 0 -3px 0 var(--orange-dark)}
.news-bar{left:0;top:487px;width:1200px;height:44px;background:var(--orange);color:var(--white)}
.news-label{left:192px;top:15px;font-weight:700;font-size:10px;letter-spacing:.5px}
.news-text{left:295px;top:15px;font-size:10px;font-weight:600}
.news-sep{left:278px;top:12px;width:1px;height:20px;background:rgba(255,255,255,.5)}
.news-dots{left:962px;top:19px;display:flex;gap:6px}
.news-dots span{width:5px;height:5px;border-radius:50%;background:var(--white)}
.hero-base{left:0;top:531px;width:1200px;height:15px;background:var(--darker)}

/* headings */
.section-title{font-size:10px;font-weight:700;color:var(--dark);text-transform:uppercase;letter-spacing:.3px}
.section-title em{font-style:normal;color:var(--orange)}
.rule{height:1px;background:var(--rule);left:187px;width:826px}
p{margin-bottom:6px}

/* intro */
.intro{left:187px;top:584px;width:640px}
.lead{margin-top:12px;font-size:13.5px;line-height:19px;color:var(--muted)}
.intro-body{margin-top:6px;font-size:9.5px}
.intro-circle{top:567px;width:78px;height:78px;border-radius:50%;background:#e4e4e4;display:flex;align-items:center;justify-content:center}

/* steps */
.steps-title{left:187px;top:756px}
.step-arrow{top:902px}
.step{top:836px;width:200px;text-align:center}
.step-photo{width:180px;height:180px;border-radius:50%;margin:0 auto;border:3px solid #222;
  background:radial-gradient(circle at 50% 50%,#e2e2e2 0%,#8a8a8a 22%,#2a2a2a 45%,#6b6b6b 60%,#1a1a1a 78%,#4a4a4a 100%)}
.step-photo.accent{background:var(--orange);border-color:var(--orange);display:flex;align-items:center;justify-content:center}
.step h3{margin-top:22px;font-size:9.5px;font-weight:700;color:var(--dark)}
.step p{margin-top:5px;font-style:italic;font-size:9.5px;color:#666;padding:0 18px}

/* columns */
.col{width:392px;font-size:9.5px}
.col .section-title{margin-bottom:12px}

/* news */
.news-list{font-size:9.5px}
.news-photo{top:1505px;width:241px;height:198px;border:3px solid #111}
.news-cap{top:1722px;width:241px;text-align:center}
.news-cap h4{font-size:9.5px;font-weight:700;color:var(--dark)}
.news-cap span{font-size:8.5px;color:var(--muted)}

/* rates widget */
.rates{left:211px;top:1881px;width:773px;height:226px;border:1px solid #c9cde0;background:var(--white);box-shadow:0 2px 4px rgba(0,0,0,.12)}
.rates-head{left:10px;top:4px;font-size:22px;font-weight:700;color:var(--rate-blue);line-height:28px}
.rates-add{left:480px;top:8px;width:280px;height:18px;border:1px solid #bbb;font-size:9px;color:#c22;padding:2px 8px}
.rates-table{left:10px;top:36px;width:752px;border-collapse:collapse;font-size:11px;color:#223}
.rates-table th{font-weight:600;font-size:10px;padding:3px 0;color:#223;background:var(--rate-head)}
.rates-table td{text-align:center;padding:0;line-height:15px;font-family:"Courier New",monospace}
.rates-table tr.row td{padding-top:5px}
.rates-table tr.inv td{color:#557;padding-bottom:4px;border-bottom:1px solid #dde}
.flag{display:block;width:18px;height:12px;margin:0 auto 2px;border-radius:2px;background:linear-gradient(#c8322f 0 33%,#fff 33% 66%,#2a4aa0 66%)}
.rates-table td.lbl{text-align:left;padding-left:6px;font-family:"Open Sans",Arial,sans-serif;width:76px}
.rates-time{left:12px;top:182px;font-size:9px;color:#557}
.rates-foot{left:0;top:200px;width:771px;text-align:center;font-size:13px;font-weight:700;color:#334;background:#eef0f6;height:24px;line-height:24px}

/* footer */
.site-footer{left:0;top:2139px;width:1200px;height:320px;background:var(--dark);color:#ccc}
.footer-about{left:187px;top:45px;width:395px;font-size:10px;line-height:14px}
.newsletter{left:630px;top:54px;width:378px;height:40px;background:var(--white);display:flex;align-items:center;padding:5px}
.newsletter .field{flex:1;font-size:10px;color:#999;padding-left:24px;position:relative}
.newsletter .field svg{position:absolute;left:4px;top:0}
.newsletter .btn{background:var(--orange);color:var(--white);font-weight:700;font-size:10px;padding:7px 14px}
.footer-social{left:189px;top:133px;display:flex;gap:12px}
.copyright{left:187px;top:208px;font-size:9px;color:#aaa}
</style>
</head>
<body>

<header class="site-header abs">
  <div class="brand abs"><span class="brand-mark"></span><span class="brand-name">Norvane Exchange</span></div>
  <nav class="main-nav abs">
    <span class="active">Home</span><span>Services</span><span>Transfer</span><span>About Us</span><span>Contact Us</span><span>FAQ</span>
  </nav>
</header>

<div class="hero abs" role="img" aria-label="Black and white long-exposure photo of city traffic light trails on a highway"></div>
<div class="hero-social abs">
  <span class="circle-btn" aria-label="Social link"></span>
  <span class="circle-btn" aria-label="Social link"></span>
  <span class="circle-btn" aria-label="News feed"><svg width="16" height="16" viewBox="0 0 16 16"><circle cx="3" cy="13" r="2" fill="#fff"/><path d="M1 7a8 8 0 0 1 8 8" fill="none" stroke="#fff" stroke-width="2"/><path d="M1 2a13 13 0 0 1 13 13" fill="none" stroke="#fff" stroke-width="2"/></svg></span>
</div>
<div class="news-bar abs">
  <span class="news-label abs">LATEST NEWS</span>
  <span class="news-sep abs"></span>
  <span class="news-text abs">The Global markets continue to be dominated by expectations ...</span>
  <div class="news-dots abs"><span></span><span></span><span></span></div>
</div>
<div class="hero-base abs"></div>

<section class="intro abs">
  <h2 class="section-title">Norvane <em>Exchange Money Transfer</em></h2>
  <p class="lead">Looking to send money abroad ? Transferring money is easy with Norvane Exchange Money Transfer. It's work with your bank and it's free to sign up. Get free online quotes, competitive exchange rates, and no-fee money transfer options.</p>
  <p class="intro-body">Sending larger sums abroad should feel calm and certain. Our dealers lock in your rate, confirm every detail with you and track each payment until it lands safely in the receiving account. We hold client funds in segregated accounts and follow strict identity checks, so your money stays protected at every stage of the journey from start to finish.</p>
</section>
<span class="intro-circle abs" style="left:849px"><svg width="14" height="24" viewBox="0 0 14 24"><polyline points="12,2 2,12 12,22" fill="none" stroke="#fff" stroke-width="2"/></svg></span>
<span class="intro-circle abs" style="left:935px"><svg width="14" height="24" viewBox="0 0 14 24"><polyline points="2,2 12,12 2,22" fill="none" stroke="#fff" stroke-width="2"/></svg></span>

<h2 class="section-title steps-title abs">How transfer <em>works</em></h2>
<div class="rule abs" style="top:804px"></div>

<svg class="step-arrow abs" style="left:140px" width="24" height="40" viewBox="0 0 24 40"><polyline points="20,2 4,20 20,38" fill="none" stroke="#555" stroke-width="2"/></svg>
<svg class="step-arrow abs" style="left:1036px" width="24" height="40" viewBox="0 0 24 40"><polyline points="4,2 20,20 4,38" fill="none" stroke="#555" stroke-width="2"/></svg>

<div class="step abs" style="left:178px">
  <div class="step-photo" role="img" aria-label="Close-up photo of a vintage camera lens"></div>
  <h3>ORDER ONLINE MONEY TRANSFER</h3>
  <p>Get risk free quotes 24/7 on our secure site. If you like the quote lock it.</p>
</div>
<div class="step abs" style="left:387px">
  <div class="step-photo" role="img" aria-label="Photo of a vintage camera body" style="background:radial-gradient(circle at 45% 40%,#bdbdbd 0%,#6e6e6e 30%,#1d1d1d 55%,#5a5a5a 75%,#111 100%)"></div>
  <h3>TRANSFER YOUR FUNDS TO US</h3>
  <p>Send Us funds from your bank. Wire,EFT, ACH and more.</p>
</div>
<div class="step abs" style="left:608px">
  <div class="step-photo accent">
    <svg width="40" height="40" viewBox="0 0 40 40"><rect x="16" y="4" width="8" height="32" fill="#fff"/><rect x="4" y="16" width="32" height="8" fill="#fff"/></svg>
  </div>
  <h3>FUNDS CONVERSION</h3>
  <p>Funds are converted at the locked-in rate by Norvane Exchange money funds conversion.</p>
</div>
<div class="step abs" style="left:820px">
  <div class="step-photo" role="img" aria-label="Photo of a vintage rangefinder camera" style="background:radial-gradient(circle at 55% 55%,#d0d0d0 0%,#7a7a7a 25%,#222 50%,#8a8a8a 68%,#161616 100%)"></div>
  <h3>WE DELIVER THE FUNDS</h3>
  <p>We deliver by Wire,ACH,EFT and Draft,Send to yourself, or Organizations.</p>
</div>

<div class="rule abs" style="top:1119px"></div>

<section class="col abs" style="left:187px;top:1157px">
  <h2 class="section-title">Norvane <em>Exchange Services</em></h2>
  <p>We arrange international payments for private clients and businesses who move larger amounts across borders, with a named dealer for every account.</p>
  <p>Our rates are set close to the interbank market, and we never add hidden margins. You see the full cost before you confirm the deal.</p>
  <p>Forward contracts let you fix a rate for up to twelve months, protecting property purchases, tuition fees and supplier invoices from sudden market swings.</p>
  <p style="margin-top:22px">Cash exchange is available at our branch in all major currencies. Order ahead online and collect your notes at a time that suits you, with secure counters and trained staff ready to help every customer.</p>
  <p>Regular transfers can be scheduled monthly for pensions, salaries and family support abroad.</p>
</section>

<section class="col abs" style="left:622px;top:1157px">
  <h2 class="section-title">Discounts <em>Section</em></h2>
  <p>Clients sending more than ten thousand dollars receive preferential pricing, and the rate improves further as the amount of the transfer grows.</p>
  <p>Repeat customers and business accounts benefit from reduced fees on every payment, with volume tiers reviewed each quarter so your pricing always reflects your activity. Ask your dealer for a tailored quote before you send.</p>
  <p style="margin-top:22px">Refer a friend or colleague and both of you receive a fee-free transfer once their first payment completes, with no limit on the number of referrals you can make each year.</p>
  <p>Seasonal offers are announced by email to newsletter subscribers first.</p>
</section>

<div class="rule abs" style="top:1475px"></div>

<section class="news-list abs" style="left:187px;top:1504px;width:256px">
  <h2 class="section-title" style="margin-bottom:12px">Foreign exchange <em>currency news</em></h2>
  <p>Sterling held firm against the dollar after stronger retail figures this week.</p>
  <p>The euro eased slightly as traders awaited central bank comments.</p>
  <p>Yen volatility rose ahead of the monthly trade balance release.</p>
  <p>Commodity currencies gained as oil prices moved higher.</p>
  <p>Our dealers share a short market summary every morning.</p>
</section>

<div class="news-photo abs" style="left:472px;background:radial-gradient(ellipse 40% 55% at 50% 55%,#e8e8e8 0%,#9a9a9a 30%,#3a3a3a 65%,#0c0c0c 100%)" role="img" aria-label="Black and white photo of a lit building at night"></div>
<div class="news-photo abs" style="left:762px;background:radial-gradient(circle at 45% 55%,#cfcfcf 0%,#6a6a6a 25%,#1e1e1e 48%,#7a7a7a 62%,#0e0e0e 85%)" role="img" aria-label="Black and white photo of a vintage camera"></div>
<div class="news-cap abs" style="left:472px"><h4>FX UPDATE : US DATA SURPRISES</h4><span>26th November, 2013</span></div>
<div class="news-cap abs" style="left:762px"><h4>ECONOMICS OF NOTE</h4><span>26th November, 2013</span></div>

<div class="rule abs" style="top:1766px"></div>

<section class="abs" style="left:187px;top:1799px;width:826px;font-size:9.5px">
  <h2 class="section-title" style="margin-bottom:8px">Norvane Exchange live <em>exchange rates</em></h2>
  <p>Rates below update through the trading day and are shown for guidance only. Call or log in to lock a live rate for your transfer, with every quote held for a short confirmation window before the deal completes.</p>
</section>

<div class="rates abs">
  <div class="rates-head abs">Ratewise Live Exchange Rates</div>
  <div class="rates-add abs">Add a currency... ▾</div>
  <table class="rates-table abs">
    <tr><th></th><th><i class="flag"></i>USD</th><th><i class="flag"></i>EUR</th><th><i class="flag"></i>GBP</th><th><i class="flag"></i>INR</th><th><i class="flag"></i>AUD</th><th><i class="flag"></i>CAD</th><th><i class="flag"></i>ZAR</th><th><i class="flag"></i>NZD</th><th><i class="flag"></i>JPY</th></tr>
    <tr class="row"><td class="lbl">1 USD</td><td>1.00000</td><td>0.73499</td><td>0.61247</td><td>62.3320</td><td>1.09996</td><td>1.05770</td><td>10.1747</td><td>1.22566</td><td>101.793</td></tr>
    <tr class="inv"><td class="lbl">Inverse:</td><td>1.00000</td><td>1.36055</td><td>1.63275</td><td>0.01604</td><td>0.90912</td><td>0.94546</td><td>0.09828</td><td>0.81589</td><td>0.00982</td></tr>
    <tr class="row"><td class="lbl">1 EUR</td><td>1.36055</td><td>1.00000</td><td>0.83329</td><td>84.8062</td><td>1.49656</td><td>1.43906</td><td>13.8433</td><td>1.66759</td><td>138.495</td></tr>
    <tr class="inv"><td class="lbl">Inverse:</td><td>0.73499</td><td>1.00000</td><td>1.20006</td><td>0.01179</td><td>0.66820</td><td>0.69490</td><td>0.07224</td><td>0.59967</td><td>0.00722</td></tr>
    <tr class="row"><td class="lbl">1 GBP</td><td>1.63275</td><td>1.20006</td><td>1.00000</td><td>101.772</td><td>1.79596</td><td>1.72695</td><td>16.6128</td><td>2.00120</td><td>166.202</td></tr>
    <tr class="inv"><td class="lbl">Inverse:</td><td>0.61247</td><td>0.83329</td><td>1.00000</td><td>0.00983</td><td>0.55681</td><td>0.57905</td><td>0.06019</td><td>0.49970</td><td>0.00602</td></tr>
  </table>
  <div class="rates-time abs">Mid-market rates: 2013-11-27 14:12 UTC</div>
  <div class="rates-foot abs">Click on a rate to see a chart.</div>
</div>

<footer class="site-footer abs">
  <p class="footer-about abs">Norvane Exchange . We are a company that deals with currency exchange international money transfer. We do cash exchange and international money transfers to bank accounts all over the world.</p>
  <div class="newsletter abs">
    <span class="field"><svg width="14" height="12" viewBox="0 0 14 12"><rect x="0.5" y="0.5" width="13" height="11" fill="none" stroke="#aaa"/><polyline points="1,1 7,7 13,1" fill="none" stroke="#aaa"/></svg>Join Our Newsletter Here</span>
    <span class="btn">Join</span>
  </div>
  <div class="footer-social abs">
    <span class="circle-btn" aria-label="Social link"></span>
    <span class="circle-btn" aria-label="Social link"></span>
    <span class="circle-btn" aria-label="News feed"><svg width="16" height="16" viewBox="0 0 16 16"><circle cx="3" cy="13" r="2" fill="#fff"/><path d="M1 7a8 8 0 0 1 8 8" fill="none" stroke="#fff" stroke-width="2"/><path d="M1 2a13 13 0 0 1 13 13" fill="none" stroke="#fff" stroke-width="2"/></svg></span>
  </div>
  <p class="copyright abs">Copyright 2013 Norvane Exchange.</p>
</footer>

</body>
</html>
```